Design of a chocolate packaging

In hand-lettering-style: "Thank you for your work - you are an important part of our team!" (in big letters - almost 2/3 of the whole place) "This chocolate is a lot, so you enter into a raffle and have a great chance of a Brisk duo and many more great winnings ... all the information is below www.tlv-nachwuchsforum.de! Good luck !!! " (in small letters underneath) The place is: 7,3cm * 15,3cm (crosswise)

Font styles to use
Script

```html
<!DOCTYPE html>
<html lang="de">
<head>
<meta charset="utf-8">
<title>Schokoladen-Banderole – Danke für Deine Arbeit</title>
<link href="https://fonts.googleapis.com/css2?family=Great+Vibes&family=Lora:ital,wght@1,400;1,700&family=Oswald:wght@300&display=swap" rel="stylesheet">
<style>
  :root {
    --page: #ffffff;
    --choc-deep: #1f0904;
    --choc-dark: #2e0f07;
    --choc-mid: #5a2610;
    --choc-warm: #7a3a18;
    --caramel: #b07a4c;
    --caramel-light: #d3a77b;
    --gold-text: #c8996a;
    --heading-text: #b7875c;
  }
  html, body {
    margin: 0;
    width: 1200px;
    height: 900px;
    overflow: hidden;
    background: var(--page);
  }
  .wrapper {
    position: absolute;
    left: 25px;
    top: 176px;
    width: 1150px;
    height: 548px;
    overflow: hidden;
    background: var(--choc-dark);
  }
  .silk-backdrop {
    position: absolute;
    inset: 0;
    background:
      radial-gradient(ellipse 55% 45% at 62% 48%, rgba(150, 72, 32, 0.55), transparent 70%),
      radial-gradient(ellipse 40% 35% at 25% 30%, rgba(110, 50, 22, 0.5), transparent 70%),
      linear-gradient(160deg, var(--choc-deep) 0%, var(--choc-mid) 35%, var(--choc-warm) 55%, var(--choc-mid) 75%, var(--choc-deep) 100%);
  }
  .wave {
    position: absolute;
    inset: 0;
    width: 1150px;
    height: 548px;
  }
  .thanks-script {
    position: absolute;
    font-family: "Great Vibes", cursive;
    color: var(--caramel-light);
    text-shadow: 2px 3px 3px rgba(20, 5, 0, 0.75);
    margin: 0;
    line-height: 1;
    font-weight: 400;
  }
  .thanks-danke { left: 110px; top: 30px; font-size: 130px; }
  .thanks-deine { left: 100px; top: 160px; font-size: 128px; }
  .thanks-arbeit { left: 140px; top: 280px; font-size: 140px; }
  .team-message {
    position: absolute;
    left: 640px;
    top: 52px;
    width: 430px;
    margin: 0;
    text-align: center;
    font-family: "Lora", serif;
    font-style: italic;
    font-weight: 700;
    font-size: 54px;
    line-height: 60px;
    color: var(--heading-text);
    text-shadow: 2px 3px 2px rgba(15, 3, 0, 0.85);
    transform: rotate(-4deg);
  }
  .raffle-note {
    position: absolute;
    left: 500px;
    top: 396px;
    width: 620px;
    margin: 0;
    text-align: center;
    font-family: "Lora", serif;
    font-style: italic;
    font-size: 19px;
    line-height: 25.5px;
    color: var(--gold-text);
  }
  .site-url {
    position: absolute;
    left: 60px;
    top: 482px;
    margin: 0;
    font-family: "Oswald", sans-serif;
    font-weight: 300;
    font-size: 26px;
    letter-spacing: 4.6px;
    color: var(--gold-text);
  }
</style>
</head>
<body>
  <main class="wrapper">
    <div class="silk-backdrop" role="img" aria-label="Flowing chocolate-brown silk folds as background texture"></div>

    <svg class="wave" viewBox="0 0 1150 548" aria-hidden="true">
      <defs>
        <linearGradient id="bandGradient" x1="0" y1="0" x2="1" y2="0">
          <stop offset="0" stop-color="#8a5a36"/>
          <stop offset="0.5" stop-color="#b9865a"/>
          <stop offset="1" stop-color="#c2906a"/>
        </linearGradient>
        <linearGradient id="lowerGradient" x1="0" y1="0" x2="0" y2="1">
          <stop offset="0" stop-color="#4a1e0b"/>
          <stop offset="1" stop-color="#240a04"/>
        </linearGradient>
      </defs>
      <path d="M0,390 C230,450 450,420 660,355 C840,300 1000,290 1150,305 L1150,548 L0,548 Z" fill="#3c170a" opacity="0.6"/>
      <path d="M0,436 C300,468 600,372 800,355 C960,345 1080,380 1150,440 L1150,548 L0,548 Z" fill="url(#lowerGradient)"/>
      <path d="M0,420 C250,462 470,430 680,368 C860,315 1020,305 1150,330 L1150,440 C1080,380 960,345 800,355 C600,372 300,468 0,436 Z" fill="url(#bandGradient)"/>
    </svg>

    <h1 class="thanks-script thanks-danke">Danke</h1>
    <p class="thanks-script thanks-deine">für Deine</p>
    <p class="thanks-script thanks-arbeit">Arbeit</p>

    <h2 class="team-message">Du bist ein wichtiger Teil unseres Teams!</h2>

    <p class="raffle-note">Diese Schokolade ist ein Los.<br>
      Du nimmst damit an einer Verlosung<br>
      Teil und hast großartige Chancen auf einen Brisk duo<br>
      und viele weitere tolle Gewinne...alle Infos gibt es<br>
      unter www.tlv-nachwuchsforum.de! Viel Glück!!!</p>

    <p class="site-url">www.tlv-nachwuchsforum.de</p>
  </main>
</body>
</html>
```